Construction Company looking to change the way General Contractors are perceived today

Looking for a 10-12 page professional web design that includes social media integration, contact form, multiple ways to contact us, services provided, about page, testimonials, project portfolio, downloadable resources, mobile friendly, media gallery, blog, Subcontractors/Bids tab
Must have editing abilities.
I like parallax scrolling, autoplay,
Here is a great example of a site I like. https://marlowstoneworks.com/

Target Market(s)

Commercial and Industrial Owners and Project Managers, Residential Home and Multifamily Owners, Architects and Engineers

Industry/Entity Type

Construction, Pre-construction, Construction Management

Coding

Number of Pages Required

5+ page

Colors

Designer to choose colors to be used in the design.

Requirements
Must have
• TRI-BAY GROUP (Business name) services General Contracting, Construction Management, Pre-construction Services, Home Renovations, Additions, Exterior Spaces, Commercial Construction, Interior buildouts, Office Space Renovations.
Nice to have
• Full-Service General Contractor, Family Oriented - Client Focused, Owner Involved, Relationship Focused, Superior Workmanship, Communication Driven

```html
<!DOCTYPE html>
<html lang="en">
<head>
<meta charset="utf-8">
<title>Tri-Bay Group — General Contractors</title>
<link rel="stylesheet" href="https://fonts.googleapis.com/css2?family=Bebas+Neue&family=Poppins:wght@400;500;600&display=swap">
<style>
:root{
  --blue:#0a84f0;
  --blue-deep:#0672d6;
  --ink:#1b1b1b;
  --text:#555a60;
  --white:#ffffff;
  --grey-band:#b3b3b3;
  --light:#f4f6f9;
  --black:#000000;
  --head:"Bebas Neue", "Arial Narrow", sans-serif;
  --body:"Poppins", Arial, sans-serif;
}
*{margin:0;padding:0;box-sizing:border-box}
html,body{width:1200px;height:4724px;overflow:hidden;background:var(--white)}
body{font-family:var(--body);color:var(--ink)}
.page{position:relative;width:1200px;height:4724px;overflow:hidden}
.abs{position:absolute}
.head{font-family:var(--head);font-weight:400;line-height:1;letter-spacing:.5px}
.photo{position:absolute}
.brand-text{font-family:var(--head);font-weight:400;text-align:center;line-height:1.05}

/* hero */
.hero{position:absolute;left:0;top:0;width:1200px;height:600px;background:var(--blue)}
.hero-photo{left:0;top:0;width:600px;height:600px;background:linear-gradient(160deg,#f7f3ee 0%,#ece4d8 45%,#d9c3a2 75%,#c9a77c 100%)}
.hero-line{position:absolute;font-family:var(--head);color:var(--white);font-size:42px;line-height:1;letter-spacing:.5px}
.hero-line.accent{color:var(--ink);font-size:54px}

/* nav */
.nav{position:absolute;left:92px;top:51px;width:1018px;height:50px;background:var(--white);border-radius:25px;box-shadow:0 2px 8px rgba(0,0,0,.08)}
.nav a{position:absolute;top:17px;font-size:13px;color:#333;text-decoration:none;white-space:nowrap}
.nav-logo{position:absolute;left:447px;top:-36px;width:122px;height:122px;border-radius:50%;background:var(--white);border:5px solid var(--blue);display:flex;align-items:center;justify-content:center}
.nav-logo .brand-text{color:var(--blue);font-size:24px}
.social{position:absolute;display:flex;gap:10px}
.social span{width:22px;height:22px;border-radius:50%;background:var(--blue);display:block}
.btn-contact{position:absolute;left:905px;top:9px;width:94px;height:32px;border-radius:16px;background:var(--blue);color:var(--white);font-family:var(--head);font-size:14px;display:flex;align-items:center;justify-content:center}

/* badge */
.badge{position:absolute;width:80px;height:80px}

/* about */
.label{font-family:var(--head);font-size:18px;color:#8a8a8a;letter-spacing:.5px}
.about-title{font-family:var(--head);font-size:50px;color:var(--blue);line-height:1}
.about-copy{position:absolute;left:139px;top:840px;width:398px;font-size:13px;line-height:24.6px;color:var(--text)}
.about-copy span{display:block;white-space:nowrap;text-align:justify;text-align-last:justify}
.about-copy span.last{text-align-last:left}
.about-photo{left:637px;top:679px;width:422px;height:460px;background:linear-gradient(120deg,#f4f4f2 0%,#dcd8d2 40%,#b08a5c 70%,#d6b98e 100%);z-index:2}
.stamp{position:absolute;left:548px;top:980px;width:196px;height:196px;border-radius:50%;background:var(--white);border:8px solid var(--blue);box-shadow:0 0 0 5px #c9d0d8;display:flex;align-items:center;justify-content:center;z-index:1}
.stamp .brand-text{color:var(--blue);font-size:34px}

/* portfolio */
.portfolio{position:absolute;left:0;top:1217px;width:1200px;height:2319px;background:var(--blue)}
.project-photo{width:409px;height:474px}
.cap-title{position:absolute;font-family:var(--head);font-size:26px;color:var(--white);line-height:1}
.cap-loc{position:absolute;font-size:19px;color:var(--white)}
.section-label{font-family:var(--head);font-size:19px;color:var(--white)}
.section-title{font-family:var(--head);font-size:54px;color:var(--white);line-height:1}

/* reviews */
.video{left:105px;top:3031px;width:495px;height:345px;background:linear-gradient(135deg,#cfd9e4 0%,#d9b98d 45%,#b88a5e 65%,#9eb6d2 100%)}
.play{position:absolute;left:330px;top:3184px;width:40px;height:40px}
.review-row{position:absolute;left:640px;width:391px;height:94px}
.review-row.active{border:1.5px solid var(--white)}
.review-thumb{position:absolute;left:10px;top:8px;width:102px;height:76px}
.review-name{position:absolute;left:191px;top:34px;font-size:20px;color:var(--white)}

/* services */
.services{position:absolute;left:0;top:3536px;width:1200px;height:396px;background:linear-gradient(180deg,#ffffff 0%,var(--light) 100%)}
.svc{position:absolute;top:3752px;display:flex;align-items:center;gap:22px}
.svc-icon{width:100px;height:100px;border-radius:50%}
.svc-name{font-size:16px;color:#555;line-height:24px}

/* blog */
.blog{position:absolute;left:0;top:3932px;width:1200px;height:413px;background:var(--grey-band)}
.btn-resources{position:absolute;left:103px;top:4197px;width:165px;height:31px;border-radius:16px;background:var(--blue);color:var(--white);font-family:var(--head);font-size:13px;display:flex;align-items:center;justify-content:center}
.news-overlay{position:absolute;left:840px;top:4136px;width:360px;height:120px;background:rgba(10,132,240,.85);color:var(--white);text-align:center}

/* footer */
.footer{position:absolute;left:0;top:4345px;width:1200px;height:379px;background:var(--black);color:var(--white)}
.foot-logo{position:absolute;left:104px;top:4396px;width:184px;height:184px;border-radius:50%;border:6px solid var(--white);display:flex;align-items:center;justify-content:center}
.foot-logo .brand-text{color:var(--white);font-size:36px}
.foot-title{position:absolute;font-family:var(--head);font-size:24px;color:var(--white)}
.quick-links{position:absolute;left:345px;top:4428px;list-style:none;color:var(--white)}
.quick-links li{font-size:14px;line-height:29.5px}
.field{position:absolute;background:var(--white);font-size:10px;color:#777;padding:6px 8px}
.btn-submit{position:absolute;left:697px;top:4593px;width:79px;height:25px;border-radius:13px;background:var(--blue);color:var(--white);font-size:12px;font-weight:600;display:flex;align-items:center;justify-content:center}
.contact-row{position:absolute;left:817px;display:flex;align-items:center;gap:12px;font-size:12px;line-height:16px;color:var(--white)}
.contact-icon{width:34px;height:34px;border-radius:50%;background:var(--blue);display:flex;align-items:center;justify-content:center;flex:none}
.divider{position:absolute;left:103px;top:4643px;width:994px;height:1px;background:#333}
.copyright{position:absolute;left:0;top:4672px;width:1200px;text-align:center;font-size:12px;color:var(--white)}
</style>
</head>
<body>
<div class="page">

  <section class="hero">
    <div class="photo hero-photo" role="img" aria-label="Bright living room with a beige sofa, wooden coffee table and oak staircase"></div>
    <div class="hero-line" style="left:701px;top:222px">We offer reliable</div>
    <div class="hero-line accent" style="left:800px;top:276px">“Word-of-mouth”</div>
    <div class="hero-line" style="left:701px;top:346px">Evidence of quality</div>
    <div class="hero-line" style="left:828px;top:401px">Workmanship</div>
    <svg class="badge" style="left:560px;top:406px" viewBox="0 0 80 80">
      <circle cx="40" cy="40" r="39" fill="#0a84f0"/>
      <defs><path id="ring1" d="M40,40 m-28,0 a28,28 0 1,1 56,0 a28,28 0 1,1 -56,0"/></defs>
      <text font-family="Poppins, sans-serif" font-size="8" fill="#fff"><textPath href="#ring1">Read More · Read More · Read More ·</textPath></text>
      <path d="M28 40h9M28 40l3-3M28 40l3 3M52 40h-9M52 40l-3-3M52 40l-3 3" stroke="#fff" stroke-width="1.6" fill="none"/>
    </svg>
  </section>

  <nav class="nav">
    <a style="left:40px">Home</a>
    <a style="left:101px">Our Services</a>
    <a style="left:205px">About Us</a>
    <a style="left:285px">Testimonials</a>
    <div class="nav-logo"><div class="brand-text">TRI-BAY<br>GROUP</div></div>
    <a style="left:636px">Gallery</a>
    <a style="left:711px">Blog</a>
    <div class="social" style="left:768px;top:14px"><span></span><span></span><span></span><span></span></div>
    <div class="btn-contact">Contact us</div>
  </nav>

  <section class="about">
    <div class="abs label" style="left:141px;top:680px">About Tri-Bay Group</div>
    <div class="abs about-title" style="left:139px;top:718px">Tri-Bay Group</div>
    <div class="abs about-title" style="left:284px;top:779px;z-index:3">General Contractors</div>
    <p class="about-copy">
      <span>“Lorem ipsum dolor sit amet, consectetur adipiscing elit,</span>
      <span>sed do eiusmod tempor incididunt ut labore et dolore</span>
      <span>magna aliqua. Ut enim ad minim veniam, quis nostrud</span>
      <span>exercitation ullamco laboris nisi ut aliquip ex ea</span>
      <span>commodo consequat. Duis aute irure dolor in</span>
      <span>reprehenderit in voluptate velit esse cillum dolore eu</span>
      <span class="last">fugiat nulla pariatur.</span>
    </p>
    <svg class="badge" style="left:142px;top:1037px" viewBox="0 0 80 80">
      <defs><path id="ring2" d="M40,40 m-28,0 a28,28 0 1,1 56,0 a28,28 0 1,1 -56,0"/></defs>
      <text font-family="Poppins, sans-serif" font-size="8" fill="#0a84f0"><textPath href="#ring2">Read More · Read More · Read More ·</textPath></text>
      <path d="M32 40h16M48 40l-4-4M48 40l-4 4" stroke="#0a84f0" stroke-width="1.8" fill="none"/>
    </svg>
    <div class="stamp"><div class="brand-text">TRI-BAY<br>GROUP</div></div>
    <div class="photo about-photo" role="img" aria-label="Split view of a modern interior with kitchen, staircase and wooden dining table"></div>
  </section>

  <section class="portfolio">
    <div class="abs section-label" style="left:641px;top:120px">Portfolio</div>
    <div class="abs section-title" style="left:641px;top:162px">Tri-Bay Group</div>
    <div class="abs section-title" style="left:686px;top:226px">Projects</div>

    <div class="photo project-photo" style="left:103px;top:117px;background:linear-gradient(160deg,#eceef0 0%,#d8dadd 50%,#b9b2a8 80%,#2d3a4f 100%)" role="img" aria-label="Renovated bathroom with glass shower, freestanding tub and navy vanity"></div>
    <div class="cap-title" style="left:103px;top:619px">Home Renovations</div>
    <div class="cap-loc" style="left:103px;top:653px">Nebraska ,USA</div>

    <div class="photo project-photo" style="left:642px;top:334px;background:linear-gradient(150deg,#d9b98a 0%,#f2e6d2 35%,#6f7f74 65%,#3b3a36 100%)" role="img" aria-label="Covered patio addition with lounge chair and timber columns"></div>
    <div class="cap-title" style="left:641px;top:835px">Additions</div>
    <div class="cap-loc" style="left:641px;top:869px">Nebraska ,USA</div>

    <div class="photo project-photo" style="left:103px;top:721px;background:linear-gradient(170deg,#6f7884 0%,#3d4550 40%,#1e2228 70%,#8a6a4a 100%)" role="img" aria-label="Modern two-storey house exterior with dark cladding and lit windows at dusk"></div>
    <div class="cap-title" style="left:103px;top:1222px">Exterior Spaces</div>
    <div class="cap-loc" style="left:103px;top:1257px">Nebraska ,USA</div>

    <div class="photo project-photo" style="left:642px;top:936px;background:linear-gradient(200deg,#f7e27a 0%,#c8c96a 25%,#b7c6d3 55%,#6f8aa6 100%)" role="img" aria-label="Glass office tower seen from below with sunlight through trees"></div>
    <div class="cap-title" style="left:641px;top:1438px">Commercial Construction</div>
    <div class="cap-loc" style="left:641px;top:1473px">Nebraska ,USA</div>

    <svg class="badge" style="left:107px;top:1382px" viewBox="0 0 80 80">
      <defs><path id="ring3" d="M40,40 m-28,0 a28,28 0 1,1 56,0 a28,28 0 1,1 -56,0"/></defs>
      <text font-family="Poppins, sans-serif" font-size="8" fill="#fff"><textPath href="#ring3">Read More · Read More · Read More ·</textPath></text>
      <path d="M32 40h16M48 40l-4-4M48 40l-4 4" stroke="#fff" stroke-width="1.8" fill="none"/>
    </svg>

    <div class="abs section-label" style="left:105px;top:1614px">Reviews</div>
    <div class="abs section-title" style="left:104px;top:1654px">Client</div>
    <div class="abs section-title" style="left:198px;top:1711px">Stories</div>
  </section>

  <div class="photo video" role="img" aria-label="Video testimonial from a smiling client"></div>
  <svg class="play" viewBox="0 0 40 40"><circle cx="20" cy="20" r="18" fill="none" stroke="#fff" stroke-width="2"/><path d="M16 12l12 8-12 8z" fill="#fff"/></svg>

  <div class="review-row active" style="top:3044px">
    <div class="photo review-thumb" style="background:linear-gradient(135deg,#d8c3a5,#b48a62)" role="img" aria-label="Portrait of Olivia"></div>
    <div class="review-name">Olivia</div>
  </div>
  <div class="review-row" style="top:3158px">
    <div class="photo review-thumb" style="background:linear-gradient(135deg,#f2f2f2,#c9c2bc)" role="img" aria-label="Portrait of Emma"></div>
    <div class="review-name">Emma</div>
  </div>
  <div class="review-row" style="top:3270px">
    <div class="photo review-thumb" style="background:linear-gradient(135deg,#6b5a4c,#2e2620)" role="img" aria-label="Portrait of Charlotte"></div>
    <div class="review-name">Charlotte</div>
  </div>

  <section class="services">
    <div class="abs label" style="left:0;width:1200px;text-align:center;top:83px">Our Construction Services</div>
    <div class="abs about-title" style="left:0;width:1200px;text-align:center;top:126px;font-size:54px">Tri-Bay Group Remodels</div>
  </section>
  <div class="svc" style="left:78px"><div class="photo svc-icon" style="position:relative;background:linear-gradient(135deg,#e8eaec,#a9aeb4)" role="img" aria-label="Home renovation interior"></div><div class="svc-name">Home<br>Renovations</div></div>
  <div class="svc" style="left:352px"><div class="photo svc-icon" style="position:relative;background:linear-gradient(135deg,#5d7a5a,#d9d4c8)" role="img" aria-label="Room addition with plants"></div><div class="svc-name">Additions</div></div>
  <div class="svc" style="left:623px"><div class="photo svc-icon" style="position:relative;background:linear-gradient(180deg,#b9c6d3,#5a4a3e)" role="img" aria-label="Exterior of a modern home"></div><div class="svc-name">Exterior<br>Spaces</div></div>
  <div class="svc" style="left:897px"><div class="photo svc-icon" style="position:relative;background:linear-gradient(135deg,#8a9a7a,#4f5a62)" role="img" aria-label="Commercial construction site with workers"></div><div class="svc-name">Commercial<br>Construction</div></div>

  <section class="blog">
    <div class="abs section-label" style="left:106px;top:104px;font-size:18px">Blog</div>
    <div class="abs section-title" style="left:104px;top:136px">Latest News</div>
    <p class="abs" style="left:104px;top:192px;width:290px;font-size:12px;line-height:19px;color:var(--white)">Loremipsum dolor consectetur elit, sed do eiusmod tempor incididunt ut labore et dolore magna aliqua.</p>
  </section>
  <div class="btn-resources">Downloadable resources</div>
  <div class="photo" style="left:444px;top:4022px;width:374px;height:234px;background:linear-gradient(180deg,#ecebe6 0%,#d5d3cc 60%,#8f8a80 100%)" role="img" aria-label="Sunlit room with French doors and potted plants"></div>
  <div class="photo" style="left:840px;top:4022px;width:360px;height:234px;background:linear-gradient(160deg,#8a8f96 0%,#c9c4b8 40%,#e2c347 60%,#6c7078 100%)" role="img" aria-label="Worker laying paving stones"></div>
  <div class="news-overlay">
    <div class="head" style="font-size:22px;margin-top:26px">Exterior Spaces</div>
    <p style="font-size:12px;line-height:18px;margin:6px 40px 0">Quis nostrud exercitation ullamco laboris nisi ut aliquip ex ea commodo velit</p>
  </div>

  <footer class="footer"></footer>
  <div class="foot-logo"><div class="brand-text">TRI-BAY<br>GROUP</div></div>

  <div class="foot-title" style="left:345px;top:4392px">Quick Links</div>
  <ul class="quick-links">
    <li>Home</li><li>About Us</li><li>Our Services</li><li>Testimonials</li><li>Gallery</li><li>Blog</li>
  </ul>

  <div class="foot-title" style="left:501px;top:4392px">Get in Touch</div>
  <div class="field" style="left:501px;top:4432px;width:132px;height:29px">Name :</div>
  <div class="field" style="left:639px;top:4432px;width:134px;height:29px">Phone :</div>
  <div class="field" style="left:501px;top:4472px;width:272px;height:28px">Email :</div>
  <div class="field" style="left:501px;top:4510px;width:272px;height:66px">Message :</div>
  <div class="btn-submit">Submit</div>

  <div class="foot-title" style="left:817px;top:4392px">Contact Us</div>
  <div class="contact-row" style="top:4429px">
    <span class="contact-icon"><svg width="14" height="16" viewBox="0 0 14 16"><path d="M7 1a5 5 0 0 1 5 5c0 4-5 9-5 9S2 10 2 6a5 5 0 0 1 5-5z" fill="#fff"/><circle cx="7" cy="6" r="2" fill="#0a84f0"/></svg></span>
    <span>123,Lorem ipsum tetur adipiscing<br>250</span>
  </div>
  <div class="contact-row" style="top:4479px">
    <span class="contact-icon"><svg width="14" height="14" viewBox="0 0 14 14"><path d="M3 1l2.5 3-1.5 1.5a8 8 0 0 0 4.5 4.5L10 8.5 13 11l-1.5 2C6 13 1 8 1 2.5z" fill="#fff"/></svg></span>
    <span>+1 888 888 8888</span>
  </div>
  <div class="contact-row" style="top:4523px">
    <span class="contact-icon"><svg width="16" height="12" viewBox="0 0 16 12"><rect x="1" y="1" width="14" height="10" rx="1" fill="#fff"/><path d="M1 2l7 5 7-5" stroke="#0a84f0" stroke-width="1.3" fill="none"/></svg></span>
    <span>info@tribaygroup.com</span>
  </div>

  <div class="divider"></div>
  <div class="copyright">Copyrights © 2023 Tri-Bay Group Rights Reserved. | Privacy policy</div>
  <div class="social" style="left:958px;top:4670px;gap:8px"><span></span><span></span><span></span><span></span></div>

</div>
</body>
</html>
```